Coral Reach Yachting Flyer

Coral Reach Yachting (.com) is a high end luxury and private charter company in the Cayman Islands. All info can be found on our webiste. I currently have a 4 panel roll fold flyer (Can supply working file). I am looking for a new fresh look but also need some changes as we have changes some boats, added some new charter ideas etc.

Between our website and current flyer I think the designer will get the idea. I Welcome new and fresh, I do not need it to match current website, as I may get that changed to.

We are looking for high end and simple/clean and comunicate reliability and professional with a hint of fun in the sun of course. Not whacky and tacky!!

The current PDF's of the current flyer needs a fair bit of changing (For example scuba diving panel will come out and go into a new 1 panel flyer.) I will need 3-4 other flyers too, and a bunch of other stuff in future for new businesses, but starting with this one so I can pick a designer (This is my 1st go with pixel bazaar, always did my own work, but am too busy and am not very good with creativity)

I have logo, support pictures, etc. Have uploaded the basics can email more info and changes after I find a designer. Lots of our boat pictures can be found at http://coralreachyachting.example/downloads/maple.zip

Also, we want a panel dedicated to wavedart.example as our big boat now has one onboard and our smaller boat (23') will have two and that will be a dedicated panel (Replace scuba) offering a "Wavedart Ultra Reef trip" (I will supply more info on that, once I pick a designer).

Target Market(s)

High end groups. The groups or families that will spend more to get more!!

Industry/Entity Type

It Company

```html
<!DOCTYPE html>
<html lang="en">
<head>
<meta charset="utf-8">
<title>Coral Reach Yachting Flyer</title>
<link rel="stylesheet" href="https://fonts.googleapis.com/css2?family=Arimo:wght@400;700&family=Didact+Gothic&display=swap">
<style>
:root{
  --page:#e9e6e1;
  --teal:#26b3c6;
  --teal-deep:#1fa5b8;
  --navy:#1c6f98;
  --white:#ffffff;
  --ink:#2b2b2b;
  --grey:#555555;
  --head:"Arimo", Arial, sans-serif;
  --body:"Didact Gothic", "Century Gothic", sans-serif;
}
*{box-sizing:border-box;margin:0;padding:0}
html,body{width:1200px;height:745px;overflow:hidden;background:var(--page)}
.flyer{position:absolute;left:24px;top:25px;width:1152px;height:694px;background:var(--white);box-shadow:0 2px 8px rgba(0,0,0,.25);overflow:hidden}
.block,.photo{position:absolute}

.photo-girl{left:0;top:0;width:288px;height:245px;
  background:
    linear-gradient(115deg,rgba(255,255,255,0) 0%,rgba(255,255,255,0) 22%,rgba(245,247,250,.95) 34%,rgba(236,240,244,.9) 60%,rgba(255,255,255,0) 78%),
    radial-gradient(ellipse 60% 40% at 62% 45%,rgba(240,205,180,.55),rgba(240,205,180,0) 70%),
    linear-gradient(180deg,#2f78cf 0%,#7fb4e6 30%,#dbe9f5 44%,#2fb8c9 56%,#1aa4bd 100%)}
.photo-yacht{left:0;top:488px;width:577px;height:206px;
  background:
    radial-gradient(ellipse 42% 30% at 58% 50%,rgba(255,255,255,.95),rgba(235,240,244,.85) 55%,rgba(255,255,255,0) 100%),
    radial-gradient(ellipse 30% 10% at 22% 76%,rgba(255,255,255,.8),rgba(255,255,255,0) 100%),
    linear-gradient(180deg,#3e86cf 0%,#86bde8 28%,#cfe5f4 42%,#36bccd 55%,#1aa9c2 100%)}
.photo-sea{left:577px;top:0;width:575px;height:557px;
  background:
    linear-gradient(128deg,rgba(255,255,255,0) 0%,rgba(255,255,255,0) 58%,rgba(233,238,243,.95) 66%,#f4f6f8 80%,#dde3e8 100%),
    radial-gradient(ellipse 38% 30% at 90% 12%,#3f7fd4,rgba(63,127,212,0) 100%),
    linear-gradient(165deg,#5d9fe0 0%,#9fd0ef 14%,#37b5d2 34%,#1b8fb6 62%,#2aa4c4 100%)}

.eco{left:0;top:245px;width:288px;height:243px;background:var(--navy);color:var(--white);padding:18px 15px 0 18px}
.eco h2{font:400 24px/1 var(--head);margin-bottom:7px}
.eco p{font:400 11.4px/12.2px var(--body);text-align:justify}

.why{left:288px;top:0;width:289px;height:488px;background:var(--teal);color:var(--white);padding:44px 14px 0 18px}
.why h2{font:400 24px/1 var(--head);margin-bottom:14px}
.why p{font:400 11.8px/15.4px var(--body);text-align:justify}
.why h3{font:400 24px/34px var(--head);margin:30px 0 15px 3px}
.why ul{list-style:none;margin-left:2px}
.why li{font:400 13.4px/18.3px var(--body);padding-left:13px;position:relative}
.why li::before{content:"";position:absolute;left:0;top:7px;width:6px;height:6px;border-radius:50%;background:var(--white)}

.bare{left:577px;top:0;width:288px;height:278px;background:rgba(255,255,255,.78);padding:40px 10px 0 27px;color:var(--ink)}
.bare h2{font:400 26px/1 var(--head);margin-bottom:16px}
.bare p{font:400 7.9px/13px var(--head);margin-bottom:4px}

.love{left:888px;top:40px;width:264px;font:700 44px/44px var(--head);color:var(--white);text-shadow:5px 5px 0 rgba(255,255,255,.22)}

.contact{left:577px;top:557px;width:288px;height:137px;background:var(--white);padding:28px 0 0 22px}
.contact h2{font:400 18px/1 var(--head);color:var(--teal);margin-bottom:8px}
.contact p{font:700 14px/21px var(--head);color:var(--grey)}

.brand-band{left:865px;top:557px;width:287px;height:137px;background:var(--teal-deep)}
.brand{left:896px;top:510px;width:212px;height:140px;background:var(--white);display:flex;flex-direction:column;align-items:center;justify-content:center;gap:10px;box-shadow:2px 2px 4px rgba(0,0,0,.25)}
.brand-mark{width:18px;height:18px;border-radius:50%;background:var(--ink)}
.brand-name{font:400 16px/1 var(--body);color:var(--ink);letter-spacing:.3px}
.site{left:865px;top:667px;width:287px;text-align:center;font:700 10px/1 var(--head);color:var(--white)}
</style>
</head>
<body>
<main class="flyer">
  <div class="photo photo-girl" role="img" aria-label="Young girl leaning over the bow of a white boat above turquoise water"></div>

  <section class="block eco">
    <h2>Eco-Tours</h2>
    <p>Full Moon Night Adventures...<br>Enjoy the peace and tranquility at one of many locations. A pleasant blend of relaxation and adventure under the moon.<br>Bioluminescence Night Adventures...<br>Once in a lifetime experience, you will be amazed at this light spectacle as you adventure around in this mystical world.<br>You will take a breathtaking trip across the North Sound, from Palm Harbour, with your inflatable adventure boats on board. When you get to the area where the adventure begins, you will board your private inflatables, which are very stable and easy to use for almost anyone.</p>
  </section>

  <section class="block why">
    <h2>Why Choose us?</h2>
    <p>We are a Caymanian owned company striving to offer something different to locals and tourists alike. For the past 30 years the founder of this company has enjoyed the unparalleled beauty of the Cayman Islands &amp; surrounding waters. Water skiing, diving, Rum Point....</p>
    <h3>Things To Do With Us<br>In Grand Cayman</h3>
    <ul>
      <li>Swimming and Snorkeling</li>
      <li>Bioluminescence Night Diving</li>
      <li>SS Marlow Wreck Snorkelling</li>
      <li>Deep Sea Fishing</li>
      <li>Starfish Point</li>
      <li>Tidehouse Bbq Tuesdays</li>
      <li>Purchase a vacation home</li>
      <li>Family Beach Portraits</li>
      <li>Rent your own vacation villa</li>
    </ul>
  </section>

  <div class="photo photo-yacht" role="img" aria-label="White motor yacht cruising across turquoise sea"></div>

  <div class="photo photo-sea" role="img" aria-label="Swimmer diving into clear blue water beside a white yacht bow with a captain on deck"></div>

  <section class="block bare">
    <h2>Bare Boat Rentals</h2>
    <p>Now you can rent your own boat... You choose which boat you want to rent for the day... it will be delivered to the boat ramp or beach location of your choice, it will be clean, fueled, &amp; ready to go with ice. When you are finished for the day, you will return it to</p>
    <p>the dock, we will clean it, trailer it, fuel it... no stress for you.<br>At the end of the day it is much less expensive to rent a chartered or bare boat, than it is to own a boat... that is a proven fact!!</p>
  </section>

  <h1 class="block love">SHOW<br>YOUR LOVE<br>WITH US</h1>

  <section class="block contact">
    <h2>Call us now!</h2>
    <p>345-555-0148<br>info@coralreachyachting.example<br>www.coralreachyachting.example</p>
  </section>

  <div class="block brand-band"></div>
  <div class="block brand">
    <span class="brand-mark"></span>
    <span class="brand-name">Coral Reach Yachting</span>
  </div>
  <p class="block site">www.coralreachyachting.example</p>
</main>
</body>
</html>
```